Two Wine Labels, One Red One White

We are looking to create a brand image for our wines. There are two requirements by law that we need, however beyond that, the creativity comes from the designer. Required are:
On The Red Label, Alcohol 14.1White Label Alcohol 12.5, The Size, 750ML
SO One label for the red wine with alcohol at 14.1 in a 750 ML Bottle, and one Label for white with alcohol at 12.5 in a 750 ML bottle.

Hi All:
I have some more clarity to assist in the design work.
The Brand Name of the wine is Valquine for both the red and the white
The name should appear as Valquine with the Brackets around phonetical as seen here
[val-keen] Both the word and the phonetical spelling should appear.
and can be seen on lexiquarry.com The Brand Name text can be black
Label should be very light grey, I am trying to capture a Stone grey or texture from stone, although, NOT Marble.
The Red Label, The word "Red" should be in red
The White Label, The word "White" should be in White, all the original remaining elements remain as originally posted.

I look forward to hearing from you for any additional questions.
Updates

Just added a logo Not really seeing what we are trying to achieve, maybe using the logo in the design may assist

Target Market(s)

Wine Aficionados

Requirements
Must have
• Details described in Project Description above, these are required by law. The Name of the Brand will be posted shortly. For the moment if you take the project, just place red on one label and white on the other.
Nice to have
• These two wines are from California (USA), so the Sierra Nevada Mountains could be an inspiration, to outline of California or coast line, a vineyard (of course), a vine...We are in silicon valley, so there is a map of silicon valley with the Bay and ocean, something from a map could work, or let your creativity flow and not use any of these concepts.
Should not have
• I do not not care for decorative fonts, however all else is open

```html
<!DOCTYPE html>
<html lang="en">
<head>
<meta charset="utf-8">
<title>Valquine Wine Labels – Red and White</title>
<link href="https://fonts.googleapis.com/css2?family=Questrial&family=Arimo:wght@400&display=swap" rel="stylesheet">
<style>
  :root {
    --canvas-bg: #f1f1f1;
    --stone-light: #ebeae6;
    --stone-mid: #dfddd8;
    --ink: #1a1a1a;
    --red-accent: #e8202a;
    --red-phonetic: #c9323a;
    --white-accent: #d5e024;
    --white-phonetic: #a9b22a;
    --letter-on-band: #ffffff;
  }

  * { margin: 0; padding: 0; box-sizing: border-box; }

  html, body {
    width: 1200px;
    height: 900px;
    overflow: hidden;
    background: var(--canvas-bg);
  }

  .label-pair {
    position: relative;
    width: 1200px;
    height: 900px;
  }

  .wine-label {
    position: absolute;
    top: 385px;
    width: 186px;
    height: 246px;
    background:
      radial-gradient(ellipse at 30% 25%, var(--stone-light) 0%, transparent 70%),
      radial-gradient(ellipse at 75% 80%, var(--stone-mid) 0%, transparent 75%),
      var(--stone-light);
    box-shadow: 0 1px 3px rgba(0, 0, 0, 0.12);
  }

  .wine-label--red { left: 341px; --accent: var(--red-accent); --phonetic: var(--red-phonetic); }
  .wine-label--white { left: 677px; --accent: var(--white-accent); --phonetic: var(--white-phonetic); }

  .accent-rule {
    position: absolute;
    top: 13px;
    left: 0;
    width: 100%;
    height: 6px;
    background: var(--accent);
  }

  .landscape-art {
    position: absolute;
    top: 19px;
    left: 0;
    width: 100%;
    height: 88px;
  }

  .wine-label--red .landscape-art {
    background: linear-gradient(180deg,
      #39c3d1 0%, #6fb7c4 22%, #b0474a 42%, #8d3b3e 58%,
      #3a6fb0 72%, #2a54a0 86%, #7b8a5a 100%);
  }

  .wine-label--white .landscape-art {
    background: linear-gradient(180deg,
      #2d4fb5 0%, #3b5fc0 22%, #b9a83a 42%, #d2c23f 58%,
      #2f49a8 72%, #3a55b0 86%, #c8c444 100%);
  }

  .brand-name {
    position: absolute;
    top: 124px;
    left: 0;
    width: 100%;
    text-align: center;
    font-family: "Questrial", "Century Gothic", sans-serif;
    font-size: 25px;
    font-weight: 400;
    line-height: 1;
    color: var(--ink);
  }

  .brand-phonetic {
    position: absolute;
    top: 156px;
    left: 0;
    width: 100%;
    text-align: center;
    font-family: "Questrial", "Century Gothic", sans-serif;
    font-size: 10px;
    line-height: 1;
    color: var(--phonetic);
  }

  .variety-band {
    position: absolute;
    top: 171px;
    left: 0;
    width: 100%;
    height: 29px;
    background: var(--accent);
    display: flex;
    align-items: center;
    justify-content: center;
    font-family: "Questrial", "Century Gothic", sans-serif;
    font-size: 27px;
    line-height: 1;
    color: var(--letter-on-band);
  }

  .wine-label--red .variety-band { letter-spacing: 15px; padding-left: 15px; }
  .wine-label--white .variety-band { letter-spacing: 13px; padding-left: 13px; }

  .legal-details {
    position: absolute;
    top: 216px;
    left: 0;
    width: 100%;
    text-align: center;
    font-family: "Arimo", Arial, sans-serif;
    font-size: 9px;
    line-height: 13px;
    color: var(--ink);
  }
</style>
</head>
<body>
  <main class="label-pair">
    <section class="wine-label wine-label--red" aria-label="Valquine red wine label">
      <div class="accent-rule"></div>
      <div class="landscape-art" role="img" aria-label="Painted landscape of red mountains under a turquoise sky above a blue lake"></div>
      <h1 class="brand-name">Valquine</h1>
      <p class="brand-phonetic">[val-keen]</p>
      <p class="variety-band">RED</p>
      <p class="legal-details">Alcohol 14.1<br>750мл.</p>
    </section>

    <section class="wine-label wine-label--white" aria-label="Valquine white wine label">
      <div class="accent-rule"></div>
      <div class="landscape-art" role="img" aria-label="Painted landscape of golden hills under a deep blue sky above a blue lake"></div>
      <h1 class="brand-name">Valquine</h1>
      <p class="brand-phonetic">[val-keen]</p>
      <p class="variety-band">WHITE</p>
      <p class="legal-details">Alcohol 12.5<br>750мл.</p>
    </section>
  </main>
</body>
</html>
```